Building company buisness cards

We are looking for a sharp modern new look for our business cards.
We are a New Zealand based company that specialises in house and land packages.
We have attached a photo of the current logo and would like to see if it can be improved somehow if needed.
We are open to any colours but we have chosen green at this stage.
Feel free to change the font and make the logo smarter looking.
Play with the colours and see what looks best.

We want a card that looks so good know one will want to throw it away!

Target Market(s)

Home buyers

Industry/Entity Type

Building

Contact Information for Business Card

Derek Tolvane
0217394062
dtolvane@quillmarkhomesteads.co.nz
quillmarkhomesteads.co.nz

Font styles to use
Serif
Sans Serif

Colors

Designer to choose colors to be used in the design.

Requirements
Must have
• Logo and company name on one side, details on the other side
Nice to have
• Color codes for the original green are HEX #4a8028, RGB(74,128,40), CMYK(42,0,69,50)
• Round corners, Raised and/or spot UV

```html
<!DOCTYPE html>
<html lang="en">
<head>
<meta charset="utf-8">
<title>Quillmark Homesteads — Business Cards</title>
<link rel="stylesheet" href="https://fonts.googleapis.com/css2?family=Montserrat:wght@800&family=Open+Sans:wght@400;600&family=Arimo:wght@400;700&display=swap">
<style>
  :root {
    --bg: #1c1c1c;
    --brand-green: #4a8028;
    --deep-green: #0a7a0a;
    --slate: #666666;
    --white: #ffffff;
    --paper: #ffffff;
  }
  * { margin: 0; padding: 0; box-sizing: border-box; }
  html, body { width: 1200px; height: 960px; overflow: hidden; background: var(--bg); }
  .canvas {
    width: 1200px; height: 960px;
    display: flex; flex-direction: column; align-items: center; justify-content: center;
    gap: 56px;
  }
  .card {
    width: 700px; height: 400px; border-radius: 8px; overflow: hidden; position: relative;
  }
  /* Front */
  .card--front { background: var(--brand-green); color: var(--white); }
  .front-wordmark {
    position: absolute; top: 112px; left: 0; right: 0; text-align: center;
    font-family: "Montserrat", sans-serif; font-weight: 800; font-size: 40px; line-height: 1.05;
    color: var(--white); text-transform: lowercase;
  }
  .front-rule {
    position: absolute; top: 222px; left: 265px; width: 170px; height: 2px; background: var(--white);
  }
  .front-url {
    position: absolute; top: 262px; left: 0; right: 0; text-align: center;
    font-family: "Open Sans", sans-serif; font-size: 17px; letter-spacing: 2.4px; color: var(--white);
  }
  /* Back */
  .card--back { background: var(--paper); }
  .back-shapes { position: absolute; inset: 0; }
  .back-wordmark {
    position: absolute; top: 62px; left: 120px; width: 240px; text-align: center;
    font-family: "Montserrat", sans-serif; font-weight: 800; font-size: 28px; line-height: 1.05;
    color: var(--brand-green); text-transform: lowercase;
  }
  .back-rule {
    position: absolute; top: 150px; left: 185px; width: 110px; height: 2px; background: var(--brand-green);
  }
  .contact-list {
    position: absolute; top: 212px; left: 26px; list-style: none;
    font-family: "Open Sans", sans-serif; font-size: 12.5px; color: var(--white);
  }
  .contact-list li { display: flex; align-items: center; gap: 7px; margin-bottom: 9px; }
  .contact-list svg { width: 11px; height: 11px; flex: none; }
  .person {
    position: absolute; right: 30px; top: 296px; text-align: right;
    font-family: "Arimo", sans-serif; color: var(--white);
  }
  .person-name { font-weight: 700; font-size: 20px; }
  .person-title { font-weight: 700; font-size: 18px; margin-top: 2px; }
  .person-phone {
    display: flex; align-items: center; justify-content: flex-end; gap: 7px;
    font-size: 18px; margin-top: 6px; letter-spacing: 0.5px;
  }
  .person-phone svg { width: 16px; height: 16px; }
</style>
</head>
<body>
<main class="canvas">
  <section class="card card--front" aria-label="Card front">
    <p class="front-wordmark">quillmark<br>homesteads.</p>
    <div class="front-rule"></div>
    <p class="front-url">www.quillmarkhomesteads.co.nz</p>
  </section>

  <section class="card card--back" aria-label="Card back">
    <svg class="back-shapes" viewBox="0 0 700 400" width="700" height="400" aria-hidden="true">
      <polygon class="slate-panel" points="330,190 700,300 700,400 470,400" fill="var(--slate)"/>
      <polygon class="green-band" points="0,190 330,190 440,223 200,350 0,350" fill="var(--brand-green)"/>
      <polygon class="green-wedge" points="144,400 360,285 430,400" fill="var(--deep-green)"/>
    </svg>
    <p class="back-wordmark">quillmark<br>homesteads.</p>
    <div class="back-rule"></div>
    <ul class="contact-list">
      <li>
        <svg viewBox="0 0 12 12"><rect x="1" y="2.5" width="10" height="7" rx="1" fill="none" stroke="currentColor" stroke-width="1.2"/><path d="M1.5 3l4.5 3.5L10.5 3" fill="none" stroke="currentColor" stroke-width="1.2"/></svg>
        dtolvane@quillmarkhomesteads.co.nz
      </li>
      <li>
        <svg viewBox="0 0 12 12"><circle cx="6" cy="6" r="5" fill="none" stroke="currentColor" stroke-width="1.1"/><ellipse cx="6" cy="6" rx="2.2" ry="5" fill="none" stroke="currentColor" stroke-width="1"/><path d="M1 6h10" stroke="currentColor" stroke-width="1"/></svg>
        www.quillmarkhomesteads.co.nz
      </li>
    </ul>
    <div class="person">
      <p class="person-name">Derek Tolvane</p>
      <p class="person-title">Title</p>
      <p class="person-phone">
        <svg viewBox="0 0 16 16"><circle cx="8" cy="8" r="7" fill="none" stroke="currentColor" stroke-width="1.2"/><path d="M5.5 4.5l1.5 0 .6 2-1 .8a5 5 0 0 0 2.1 2.1l.8-1 2 .6v1.5c0 .5-.5.9-1 .8A6 6 0 0 1 4.7 5.5c-.1-.5.3-1 .8-1z" fill="currentColor"/></svg>
        0217394062
      </p>
    </div>
  </section>
</main>
</body>
</html>
```